Marwick Family Chiropractic Stationary

The letterhead and business card must have our logo.
We would like to see the logo used in different ways ( It can be expanded upon in the stationary.)
Please use the the same or similar colors.
Must be eye catching and memorable.
Must be easy to read

Reason: The doctor has been too busy to make any final decisions. He would like to give himself a little more time.

Target Market(s)

Chiropractic Healthcare

Industry/Entity Type

Business

Requirements
Must have
• Dr. Leonard Marwick D.C.
Chiropractor

860-555-0183

417 Birchfield Road, Suite 3
Larkfield, VT 06091

drmarwick@marwickspine.example
www.marwickspine.example
www.facebook.com/MarwickFamilySpine
Should not have
• should not be difficult to read

```html
<!DOCTYPE html>
<html lang="en">
<head>
<meta charset="utf-8">
<title>Marwick Family Chiropractic – Business Cards</title>
<link href="https://fonts.googleapis.com/css2?family=PT+Sans:wght@400;700&family=Montserrat:wght@600;700&family=Questrial&display=swap" rel="stylesheet">
<style>
  :root {
    --backdrop: #6e3b22;
    --card-black: #0b0b0b;
    --lime: #a6cf5a;
    --lime-soft: #b2d66a;
    --taupe: #8f857c;
    --white: #ffffff;
    --ink: #1a1a1a;
  }
  * { box-sizing: border-box; margin: 0; padding: 0; }
  html, body { width: 1200px; height: 716px; overflow: hidden; }
  body { background: var(--backdrop); position: relative; font-family: "PT Sans", sans-serif; }

  .card {
    position: absolute;
    width: 544px;
    height: 308px;
    border-radius: 22px;
    overflow: hidden;
    background: var(--card-black);
  }
  .card--front { left: 43px; top: 36px; }
  .card--logo-dark { left: 619px; top: 36px; }
  .card--name-back { left: 43px; top: 370px; }
  .card--logo-light { left: 619px; top: 368px; background: var(--lime); }

  /* front */
  .brand-block {
    position: absolute; left: 40px; top: 30px; width: 210px;
    text-align: center;
    font-family: "Montserrat", sans-serif;
  }
  .brand-block .dot {
    width: 80px; height: 80px; border-radius: 50%;
    background: var(--lime); margin: 0 auto 18px;
  }
  .brand-block .name { font-size: 30px; font-weight: 700; letter-spacing: 1px; line-height: 1; color: var(--lime); }
  .brand-block .tag { font-size: 11.5px; font-weight: 700; letter-spacing: .3px; margin-top: 5px; color: var(--taupe); }

  .divider {
    position: absolute; left: 257px; top: 42px; width: 2px; height: 150px;
    background: linear-gradient(to bottom, transparent, #cfcfcf 30%, #cfcfcf 70%, transparent);
  }
  .person { position: absolute; left: 285px; top: 42px; }
  .person .doctor { color: var(--lime); font-size: 17px; font-weight: 700; }
  .person .role { color: var(--taupe); font-size: 14px; margin-top: 1px; }

  .contact-list { position: absolute; left: 285px; top: 105px; list-style: none; }
  .contact-list li {
    display: flex; align-items: center; gap: 6px;
    color: #e6e6e6; font-size: 13.5px; height: 21.5px;
  }
  .contact-list svg { width: 10px; height: 10px; flex: none; }

  .swoosh { position: absolute; left: 0; top: 0; width: 544px; height: 308px; }
  .address {
    position: absolute; left: 34px; top: 256px;
    color: var(--ink); font-size: 13.5px; line-height: 20px;
  }

  /* logo cards */
  .mark-stack {
    position: absolute; left: 0; right: 0; top: 40px;
    text-align: center; font-family: "Montserrat", sans-serif;
  }
  .mark-stack .dot {
    width: 160px; height: 160px; border-radius: 50%; margin: 0 auto 14px;
  }
  .mark-stack .name { font-size: 17px; font-weight: 600; letter-spacing: 1.5px; }
  .card--logo-dark .dot { background: var(--lime); }
  .card--logo-dark .name { color: var(--lime); }
  .card--logo-light .dot { background: var(--white); }
  .card--logo-light .name { color: var(--white); }

  .web {
    position: absolute; left: 0; right: 0; top: 259px;
    text-align: center; color: var(--white);
    font-family: "Questrial", sans-serif; font-size: 14px; letter-spacing: 2.4px;
  }

  /* name back */
  .pattern-field {
    position: absolute; inset: 0;
    background: radial-gradient(ellipse at center, #1e2413 0%, #121410 60%, #0b0b0b 100%);
  }
  .wordmark {
    position: absolute; left: 0; right: 0; top: 92px;
    text-align: center;
    font-family: "Montserrat", sans-serif; font-weight: 700;
  }
  .wordmark .big { font-size: 64px; line-height: 1; letter-spacing: 2px; color: var(--lime-soft); }
  .wordmark .sub { font-size: 25px; letter-spacing: .5px; margin-top: 6px; color: var(--taupe); }
</style>
</head>
<body>

  <section class="card card--front">
    <svg class="swoosh" viewBox="0 0 544 308" aria-hidden="true">
      <path d="M0 240 C150 246 250 288 400 282 C470 279 520 270 544 262 L544 308 L0 308 Z" fill="var(--lime)"/>
      <path d="M0 232 C150 236 260 282 410 272 C480 268 520 258 544 250" fill="none" stroke="#9a9a9a" stroke-width="2"/>
      <path d="M120 238 C220 250 300 276 420 266 C480 262 520 252 544 244" fill="none" stroke="var(--lime)" stroke-width="3"/>
    </svg>

    <div class="brand-block">
      <div class="dot"></div>
      <div class="name">MARWICK</div>
      <div class="tag">FAMILY CHIROPRACTIC</div>
    </div>

    <div class="divider"></div>

    <div class="person">
      <p class="doctor">Dr. Leonard Marwick D.C.</p>
      <p class="role">Chiropractor</p>
    </div>

    <ul class="contact-list">
      <li>
        <svg viewBox="0 0 10 10"><circle cx="5" cy="5" r="4.5" fill="none" stroke="var(--lime)"/><path d="M3.3 2.6l1 1-.6.7c.4.8 1 1.4 1.7 1.7l.7-.6 1 1-.8.8C4.6 7 3 5.4 2.6 3.4z" fill="var(--lime)"/></svg>
        860-555-0183
      </li>
      <li>
        <svg viewBox="0 0 10 10"><rect x="0.5" y="2" width="9" height="6.5" rx="1" fill="var(--lime)"/><path d="M1 2.5l4 3 4-3" fill="none" stroke="#0b0b0b" stroke-width=".9"/></svg>
        mymarwick@marwickspine.example
      </li>
      <li>
        <svg viewBox="0 0 10 10"><circle cx="5" cy="5" r="4.5" fill="var(--lime)"/><path d="M.5 5h9M5 .5c-2.4 2.6-2.4 6.4 0 9M5 .5c2.4 2.6 2.4 6.4 0 9" fill="none" stroke="#0b0b0b" stroke-width=".7"/></svg>
        www.marwickspine.example
      </li>
      <li>
        <svg viewBox="0 0 10 10"><rect x="0.5" y="0.5" width="9" height="9" rx="1" fill="#3b64b0"/></svg>
        MarwickFamilySpine
      </li>
    </ul>

    <p class="address">417 Birchfield Road<br>Suite 3, Larkfield, VT 06091</p>
  </section>

  <section class="card card--logo-dark">
    <div class="mark-stack">
      <div class="dot"></div>
      <div class="name">MARWICK FAMILY CHIROPRACTIC</div>
    </div>
    <p class="web">www.marwickspine.example</p>
  </section>

  <section class="card card--name-back">
    <div class="pattern-field" role="img" aria-label="Repeating pattern of small tree emblems in dark green and amber"></div>
    <div class="wordmark">
      <div class="big">MARWICK</div>
      <div class="sub">FAMILY CHIROPRACTIC</div>
    </div>
    <p class="web">www.marwickspine.example</p>
  </section>

  <section class="card card--logo-light">
    <div class="mark-stack">
      <div class="dot"></div>
      <div class="name">MARWICK FAMILY CHIROPRACTIC</div>
    </div>
    <p class="web">www.marwickspine.example</p>
  </section>

</body>
</html>
```